Website for a financial survey consultancy

WHO WE ARE
We're a niche HR consultancy specialising in salary comparison surveys for the financial asset management industry. We position ourselves as a small, highly responsive organisation with a strong personal relationship with each of our 50+ blue-chip clients.

WHAT WE DO
Our business is 80% surveys (= products), 20% consultancy (= services). The surveys are a set of online products which clients interact with to find the information they are interested in.

WHAT WE WANT
We are completely revising our existing marketing website and need a new up-to-date look and feel for the site. We want you to design 2 web pages
- Home page
- Internal content page

More details below in Must Have Priorities.

REFERENCE SITES
- www.veltramoor.com - nice background image
- www.plimweather.com - ignoring the animations
- www.gasketvale.com
- www.quorbin.com - clean, fresh, styly but prob not corporate enough
- www.dulveropinex.com - spacious, beautiful, slightly dated tho
- www.tambly.co.uk - ignore the colours. Like the simplicity, larger font size (although want to stick with sans-serif fonts for main content)

DELIVERABLES
The final designs should be delivered as one or more PSD files with clearly named layers. All design elements and treatments should be separated out, for example use adjustment layers rather than applied (and subsequently irreversible) adjustments, strokes, shading, etc.

WHAT NEXT
I'll be monitoring the contest every day and can respond to questions fast. You can IM me on Chatterlyne or QBX.

Reason: Hi folks,

I am extending the deadline to this project as I am travelling this week and therefore will not be able to make a final decision until next Monday. I will try and provide further feedback over the course of this week but I am only going to be online occasionally so be prepared to wait a few days for a reply from me.

Thanks for all the designs so far.

Tobias

Target Market(s)

In order of importance, most important first

1. Potential customers - UK & US financial industry HR professionals, short on time. Heard about us already, want to find out more about what we do, confirm relevance for their needs. Core goal - establish credibility: are we properly resourced, will we be around for years to come, are we *real*.

2. Existing customers - UK & US financial industry professionals, short on time, under pressure, want results quickly, minimum faff, expect high quality, slickly presented information. Primary action: login and use surveys.

3. Industry professionals/researchers - probably arriving through blog content, looking to browse and hoover information. Valuable for their ability to spread awareness of who we are amongst their peers.

Industry/Entity Type

Financial

Requirements
Must have
• GENERAL
Style cues - Corporate, professional, financial, stylish, slick, clean, spacious, light
Size - standard 960px grid

NAVIGATION
- [ Home | About us | Surveys | Consulting | Blog ]
- Sub-nav (roll-over dropdown) on About Us, Surveys & Consulting

ALL PAGES
- Site navigation
- Client login (on screen permanently or link to ajaxy in-page pop-up)
- Footer section
- Existing logo (attached)* - this is obviously an important reference point in the design, esp colour

HOME PAGE
- Communicate (link thru to?) survey/consulting split
- Large photo(s)/backdrop (2-3 interchangeable options ideally). Please consider what rights agreement will be necessary for any photos you include in your design.
- Possibly bigger more prominent version of logo
- Strap line/sentence - "Focussed data is the key to success"
- 3 recent blog posts (should look good with and without blog post images)
- Free downloadable PDF research report + supporting blurb

INTERNAL PAGE
- Page title
- Content - typical page will be less than one screenfull
- Level 1 sub-heading
- Level 2 sub-heading
- Bulleted list
- Content supporting image (any image will do - interested in placement, borders (if any), spacing, caption, etc)
- 'Do something' button

* Note: there is some internal debate about this logo at the moment. Some (me) are keen for it to change, some (not me!) are not. If you have an web page design idea/concept that requires an evolution of the logo, go ahead and evolve it. We can explore this further in the design process as necessary, but don't sweat it.
Nice to have
• Values to communicate
- Knowledgeable
- Professional
- Secure
- Personal
- Experienced
- Financial industry specific
- Accurate
- Reliable
Should not have
• - Search box
- Social media links, other than RSS feed button (discrete)

```html
<!DOCTYPE html>
<html lang="en">
<head>
<meta charset="utf-8">
<title>About Us – Calverin</title>
<link rel="stylesheet" href="https://fonts.googleapis.com/css2?family=Arimo:wght@400;700&family=Tenor+Sans&display=swap">
<style>
  :root{
    --brand-red:#680a0a;
    --sky-top:#86bedf;
    --sky-bottom:#bdd3dc;
    --panel:#f8f8f8;
    --nav-bg:#dcdcdc;
    --body-blue:#286890;
    --text-grey:#333333;
    --footer-bg:#ffffff;
    --footer-bar:#262626;
    --rule:#b9b9b9;
    --button-blue:#6fa7cb;
  }
  *{margin:0;padding:0;box-sizing:border-box}
  html,body{width:1200px;height:892px;overflow:hidden}
  body{position:relative;font-family:"Arimo",Arial,sans-serif;background:var(--footer-bg)}
  .sky{position:absolute;left:0;top:0;width:1200px;height:697px;background:linear-gradient(var(--sky-top),var(--sky-bottom))}
  .client-login{position:absolute;left:968px;top:7px;width:84px;height:31px;background:linear-gradient(#8fc0de,#5f9cc2);color:#fff;font-size:13.5px;line-height:31px;text-align:center}
  .brand{position:absolute;left:167px;top:41px;width:120px}
  .brand-square{width:120px;height:116px;background:var(--brand-red)}
  .brand-name{margin-top:12px;font-family:"Tenor Sans",sans-serif;font-size:30px;color:var(--brand-red);text-align:center}
  .site-nav{position:absolute;left:168px;top:321px;width:119px;list-style:none}
  .site-nav li{height:37px;margin-bottom:1px;background:var(--nav-bg);font-family:"Tenor Sans",sans-serif;font-size:13.5px;line-height:37px;padding-left:19px;color:var(--brand-red);border-bottom:1px solid #b7cfdb}
  .site-nav li.current{background:var(--brand-red);color:#fff}
  .page-title{position:absolute;left:305px;top:121px;font-family:"Arimo",sans-serif;font-weight:400;font-size:20.5px;color:#fff}
  .title-rule{position:absolute;left:304px;top:154px;width:748px;height:4px;background:var(--brand-red)}
  .hero{position:absolute;left:304px;top:158px;width:748px;height:163px;background:linear-gradient(90deg,#b8d3ea,#d9e7f3 45%,#9fc1e2)}
  .content{position:absolute;left:304px;top:321px;width:748px;height:362px;background:var(--panel);padding:17px 10px 0 10px}
  .content h2{font-family:"Tenor Sans",sans-serif;font-weight:400;font-size:13.5px;color:var(--brand-red);margin-left:2px}
  .content p{font-size:11.2px;line-height:17px;color:var(--body-blue);margin-top:2px}
  .content h2.second{margin-top:20px}
  .bullets{list-style:none;margin-top:3px}
  .bullets li{font-size:11.2px;line-height:18.8px;color:var(--text-grey);padding-left:21px;position:relative}
  .bullets li::before{content:"";position:absolute;left:4px;top:6px;border-left:4px solid var(--brand-red);border-top:3px solid transparent;border-bottom:3px solid transparent}
  .content p.closing{margin-top:9px}
  .footer-col{position:absolute;top:714px}
  .footer-col h3{font-weight:400;font-size:15.5px;color:var(--brand-red)}
  .blog{left:168px;width:252px}
  .post{position:relative;padding-left:11px;font-size:11.2px;line-height:14.5px;color:var(--text-grey);height:43px;margin-top:6px;border-bottom:1px solid var(--rule)}
  .post:last-child{border-bottom:none}
  .post::before{content:"";position:absolute;left:2px;top:3px;border-left:5px solid var(--brand-red);border-top:4px solid transparent;border-bottom:4px solid transparent}
  .learn-more{font-size:9px;color:var(--brand-red);border-bottom:1px solid var(--brand-red)}
  .download{left:459px;width:250px}
  .download p{font-size:11.2px;line-height:15px;color:var(--text-grey);margin-top:6px;padding-left:2px}
  .report-button{position:absolute;left:458px;top:816px;width:246px;height:48px;border-radius:3px;background:linear-gradient(#8ebfdd,var(--button-blue));display:flex;align-items:center}
  .report-icon{width:40px;height:40px;margin-left:4px;background:#c23225;border-radius:2px}
  .report-text{margin-left:17px;color:#fff;font-weight:700;font-size:15.5px;line-height:14px}
  .contact{left:732px;width:200px}
  .contact address{font-style:normal;font-size:11.2px;line-height:15px;color:var(--text-grey);margin-top:6px;padding-left:2px}
  .copyright{position:absolute;left:734px;top:850px;font-size:9.5px;color:var(--brand-red)}
  .footer-brand{position:absolute;left:980px;top:714px;width:73px;height:154px}
  .footer-brand .square{width:73px;height:73px;background:var(--brand-red)}
  .footer-brand .name{margin-top:8px;font-family:"Tenor Sans",sans-serif;font-size:17px;color:var(--brand-red);text-align:center}
  .footer-bar{position:absolute;left:0;top:883px;width:1200px;height:9px;background:var(--footer-bar)}
</style>
</head>
<body>
  <div class="sky"></div>
  <a class="client-login">Client Login</a>

  <div class="brand">
    <div class="brand-square"></div>
    <div class="brand-name">Calverin</div>
  </div>

  <ul class="site-nav">
    <li>HOME</li>
    <li class="current">ABOUT US</li>
    <li>SURVEYS</li>
    <li>CONSULTING</li>
    <li>BLOG</li>
  </ul>

  <h1 class="page-title">ABOUT US</h1>
  <div class="title-rule"></div>
  <div class="hero" role="img" aria-label="Business people shaking hands in front of a pale blue world map"></div>

  <main class="content">
    <h2>VESTIBULUM ALIQUET VOLUTPAT</h2>
    <p>Lorem ipsum dolor sit amet, consectetur adipiscing elit. Nunc sed lorem dui. Sed quis nulla ac mauris lobortis imperdiet. Mauris quis augue in arcu pulvinar sollicitudin id non tellus. Sed sit amet orci sed arcu viverra vehicula. Phasellus in nibh nisl. Aenean non nisl quam. Phasellus id purus non eros pretium sagittis. Aenean in aliquam lectus. Duis blandit est rutrum libero pulvinar non elementum dui tristique. Morbi sit amet nibh mauris, in mattis ipsum. Ut placerat molestie ipsum lobortis tincidunt. Mauris non nulla massa.</p>
    <h2 class="second">CONSECTETUR ARDIPISCING</h2>
    <ul class="bullets">
      <li>Lorem ipsum dolor sit amet, consectetur adipiscing elit.</li>
      <li>Vestibulum aliquet volutpat velit, id fringilla arcu dignissim nec.</li>
      <li>Donec pulvinar mi fringilla tellus semper ac varius nisl posuere.</li>
      <li>Cras aliquam semper diam, ut lacinia ipsum semper ut.</li>
      <li>Sed porta blandit enim, id suscipit purus aliquet ac.</li>
      <li>Nunc congue felis mollis augue convallis accumsan.</li>
      <li>Proin eu nisi nulla, sit amet tincidunt sapien.</li>
    </ul>
    <p class="closing">Duis blandit est rutrum libero pulvinar non elementum dui tristique. Morbi sit amet nibh mauris, in mattis ipsum. Ut placerat molestie ipsum lobortis tincidunt. Mauris non nulla massa. Lorem ipsum dolor sit amet, consectetur adipiscing elit. Nunc sed lorem dui. Sed quis nulla ac mauris lobortis imperdiet. Mauris quis augue in arcu pulvinar sollicitudin id non tellus.</p>
  </main>

  <section class="footer-col blog">
    <h3>BLOG</h3>
    <div class="post">Lorem ipsum dolor sit amet, consectetur adipiscing elit. <span class="learn-more">LEARN MORE</span></div>
    <div class="post">Morbi a purus vel sem accumsan varius eget ut erat. <span class="learn-more">LEARN MORE</span></div>
    <div class="post">Class aptent taciti sociosqu ad litora torquent per conubia nostra. <span class="learn-more">LEARN MORE</span></div>
  </section>

  <section class="footer-col download">
    <h3>FREE Download</h3>
    <p>er inceptos himenaeos. Pellentesque habitant morbi tristique senectus et netus et malesuada fames ac turpis egestas. Aliquam erat volutpat. Maecenas dapibus</p>
  </section>
  <a class="report-button">
    <span class="report-icon"></span>
    <span class="report-text">RESEARCH REPORT +<br>SUPPORTING BLURB</span>
  </a>

  <section class="footer-col contact">
    <h3>Contact Us</h3>
    <address>Calverin<br>Suite 200 - 875 Larkfield Rd. N.W.<br>Cityname, State Name<br>USA<br><br>E-mail: contact@calverin.com</address>
  </section>
  <div class="copyright">© 2011 Calverin.com. All rights reserved</div>

  <div class="footer-brand">
    <div class="square"></div>
    <div class="name">Calverin</div>
  </div>

  <div class="footer-bar"></div>
</body>
</html>
```